TalkHarbor - Language Coaching Services

Sleek, innovative, trendy design for Language Coaching business.

TalkHarbor is a new UK based company that provides Language Coaching services. We offer highly personalized on-line and face to face language courses. We also impart learning techniques workshops based on the latest neuroscience research for second-language acquisition.

Target Market(s)

See attached info

Industry/Entity Type

Consulting

Contact Information for Business Card

TalkHarbor
DaniaKV@talkharbor.co.uk
TalkHarbor.co.uk
London, UK

Font styles to use
Sans Serif

```html
<!DOCTYPE html>
<html lang="en">
<head>
<meta charset="utf-8">
<title>TalkHarbor Business Card</title>
<link rel="stylesheet" href="https://fonts.googleapis.com/css2?family=Montserrat:wght@300;400;700&display=swap">
<style>
  :root {
    --page-bg: #e6e6e6;
    --card-white: #ffffff;
    --brand-blue: #0a78ad;
    --brand-cyan: #1aa3d9;
    --title-grey: #8a8a8a;
    --body-grey: #555555;
    --back-light: #00b6ee;
    --back-mid: #0a8ec8;
    --back-dark: #005a8a;
  }
  * { margin: 0; padding: 0; box-sizing: border-box; }
  html, body {
    width: 1125px; height: 1200px; overflow: hidden;
    background: var(--page-bg);
    font-family: "Montserrat", sans-serif;
  }
  .card {
    position: absolute;
    left: 150px;
    width: 825px;
    height: 471px;
    border-radius: 26px;
    overflow: hidden;
  }
  .card-front { top: 98px; background: var(--card-white); }
  .card-back {
    top: 630px;
    background: radial-gradient(ellipse 520px 420px at 42% 50%, var(--back-light) 0%, var(--back-mid) 45%, var(--back-dark) 100%);
  }

  .front-brand {
    position: absolute;
    left: 440px; top: 44px; width: 340px;
    text-align: center;
  }
  .brand-dot {
    display: block;
    width: 134px; height: 134px;
    margin: 0 auto 14px;
    border: 9px solid var(--brand-cyan);
    border-radius: 50%;
  }
  .brand-name {
    font-weight: 400;
    font-size: 46px;
    letter-spacing: 1px;
    color: var(--brand-cyan);
    line-height: 1;
  }

  .person { position: absolute; left: 50px; top: 235px; }
  .person-name {
    font-weight: 700; font-size: 29px; letter-spacing: 0.5px;
    color: var(--brand-blue); line-height: 1.1;
  }
  .person-title {
    font-weight: 700; font-size: 20px; letter-spacing: 0.5px;
    color: var(--title-grey); line-height: 1.2;
  }
  .contact-list { position: absolute; left: 50px; top: 314px; list-style: none; }
  .contact-list li {
    display: flex; align-items: center;
    font-weight: 400; font-size: 19.5px; color: var(--body-grey);
    height: 26px;
  }
  .contact-list li.gap { margin-bottom: 12px; }
  .contact-list svg { width: 18px; height: 20px; margin-right: 12px; fill: var(--brand-blue); }

  .back-brand {
    position: absolute; right: 86px; top: 345px; text-align: right;
  }
  .back-brand .brand-name { color: #ffffff; font-size: 48px; }
  .back-web {
    margin-top: 6px;
    font-weight: 400; font-size: 18px; letter-spacing: 5px;
    color: #ffffff;
  }
</style>
</head>
<body>
  <section class="card card-front">
    <div class="front-brand">
      <span class="brand-dot"></span>
      <div class="brand-name">TALKHARBOR</div>
    </div>

    <div class="person">
      <h1 class="person-name">OWEN BLAKE</h1>
      <p class="person-title">CEO/FOUNDER</p>
    </div>

    <ul class="contact-list">
      <li class="gap">
        <svg viewBox="0 0 18 20" aria-hidden="true"><path d="M9 0a7 7 0 0 0-7 7c0 5 7 13 7 13s7-8 7-13a7 7 0 0 0-7-7zm0 10a3 3 0 1 1 0-6 3 3 0 0 1 0 6z"/></svg>
        London, UK
      </li>
      <li>
        <svg viewBox="0 0 18 20" aria-hidden="true"><path d="M4 0h10a1.5 1.5 0 0 1 1.5 1.5v17A1.5 1.5 0 0 1 14 20H4a1.5 1.5 0 0 1-1.5-1.5v-17A1.5 1.5 0 0 1 4 0zm0.5 2.5v13h9v-13zM9 16.5a1 1 0 1 0 0 2 1 1 0 0 0 0-2z"/></svg>
        555 201 7846
      </li>
      <li>
        <svg viewBox="0 0 18 20" aria-hidden="true"><path d="M0 5h18v11H0zm1.5 1.5v.6L9 12l7.5-4.9v-.6zm0 2.4v5.6h15V8.9L9 13.8z"/></svg>
        DaniaKV@talkharbor.co.uk
      </li>
      <li>
        <svg viewBox="0 0 18 20" aria-hidden="true"><path d="M9 2a8 8 0 1 0 0 16A8 8 0 0 0 9 2zm-1 3c-1 1-3 1-3 3s2 1 2 3-1 2-1 4c-2-1-3-3-3-5a6 6 0 0 1 5-5zm3 10c0-2 2-2 2-4s-2-1-2-3l1-2a6 6 0 0 1-1 9z"/></svg>
        TalkHarbor.co.uk
      </li>
    </ul>
  </section>

  <section class="card card-back">
    <div class="back-brand">
      <div class="brand-name">TALKHARBOR</div>
      <div class="back-web">www.TalkHarbor.co.uk</div>
    </div>
  </section>
</body>
</html>
```